Real Estate Acquisition Company Needs Business Card Design

Bellwick Real Estate is in need of a business card design!

As a Real Estate Acquisition Company, Bellwick Real Estate conducts mutually beneficial real estate transactions that actively consider the needs of the seller. At Bellwick Real Estate we’re actively buying properties from those that see value in a direct transaction, but more importantly want reassurances that they, personally, are in integral part of it. Of course, it all starts with fair market value, but it doesn’t stop there. We’ve found the most success when we offer more. And with our deep experience in this industry, we’ve discovered that we have a lot to offer!

We already have a logo and brand guidelines that we've uploaded. Our final design should stay true to the guidelines. We are looking for a business card design that has two names (Ex. Jane Doe & John Doe) and contact information for each person- this way the company principals can share a card as they often do business as a team.
Updates

The criteria was unfortunately not met on most designs. We are looking for a card that has a layout for TWO names and respective contact information for each of the two people. Almost all designs only had a space for one name and one set of contact information.

Industry/Entity Type

Real Estate

Contact Information for Business Card

We are looking for a business card design that has two names (Ex. Jane Doe & John Doe) and each of their contact information- this way the company principals can share a card as they often do business as a team.

Font styles to use
Other font styles liked:
• Use Brand Guidelines

Requirements
Must have
• Please stay true to our Brand Guidelines for colours, fonts, and positioning of logo.

We require a layout for two names and respective contact information. The company principals work as a team and want a card that has both their information on it.

```html
<!DOCTYPE html>
<html lang="en">
<head>
<meta charset="UTF-8">
<title>Bellwick Real Estate – Business Card</title>
<link href="https://fonts.googleapis.com/css2?family=Lato:wght@400;700;900&display=swap" rel="stylesheet">
<style>
  :root {
    --navy: #17213a;
    --gold: #f0ac32;
    --white: #ffffff;
    --backdrop: #e6e7ea;
    --ink: #17213a;
  }
  html, body {
    margin: 0;
    padding: 0;
    width: 1200px;
    height: 900px;
    overflow: hidden;
    background: var(--backdrop);
    font-family: "Lato", Arial, sans-serif;
  }
  .canvas {
    position: relative;
    width: 1200px;
    height: 900px;
  }
  .card {
    position: absolute;
    width: 700px;
    height: 400px;
    border-radius: 18px;
    overflow: hidden;
    box-shadow: 0 6px 18px rgba(23, 33, 58, 0.18);
  }
  .card--front {
    left: 60px;
    top: 30px;
    background: var(--white);
  }
  .card--back {
    right: 60px;
    bottom: 30px;
    background: var(--navy);
    display: flex;
    align-items: center;
    justify-content: center;
  }
  .edge-band {
    position: absolute;
    left: 0;
    right: 0;
    bottom: 0;
    height: 26px;
    background: var(--navy);
  }
  .edge-line {
    position: absolute;
    left: 0;
    right: 0;
    bottom: 34px;
    height: 3px;
    background: var(--gold);
  }
  .brand {
    font-weight: 700;
    line-height: 1;
    letter-spacing: 0.02em;
    text-transform: uppercase;
  }
  .brand__name {
    display: block;
    font-size: 92px;
  }
  .brand__sub {
    display: block;
    font-size: 26px;
    letter-spacing: 0.14em;
    margin-top: 12px;
    text-align: right;
  }
  .card--front .brand {
    position: absolute;
    right: 48px;
    top: 34px;
    color: var(--navy);
  }
  .card--front .brand__name {
    font-size: 76px;
  }
  .card--front .brand__sub {
    font-size: 22px;
    margin-top: 10px;
  }
  .card--back .brand {
    color: var(--white);
  }
  .team {
    position: absolute;
    left: 48px;
    right: 48px;
    top: 190px;
    display: grid;
    grid-template-columns: 1fr 1fr;
    column-gap: 40px;
    color: var(--ink);
  }
  .person {
    display: flex;
    flex-direction: column;
  }
  .person__name {
    font-size: 24px;
    font-weight: 700;
    line-height: 1.1;
  }
  .person__role {
    font-size: 15px;
    margin-top: 4px;
    padding-bottom: 10px;
    border-bottom: 2px solid var(--gold);
    width: 60px;
  }
  .contacts {
    list-style: none;
    margin: 10px 0 0;
    padding: 0;
    font-size: 15px;
    font-weight: 700;
  }
  .contacts li {
    display: flex;
    align-items: center;
    gap: 9px;
    margin: 5px 0;
    white-space: nowrap;
  }
  .contacts svg {
    width: 14px;
    height: 14px;
    fill: var(--navy);
    flex: none;
  }
</style>
</head>
<body>
<main class="canvas">
  <section class="card card--front" aria-label="Card front">
    <div class="brand">
      <span class="brand__name">Bellwick</span>
      <span class="brand__sub">Real Estate Inc.</span>
    </div>
    <div class="team">
      <div class="person">
        <span class="person__name">John Doe</span>
        <span class="person__role">CEO</span>
        <ul class="contacts">
          <li>
            <svg viewBox="0 0 24 24" aria-hidden="true"><path d="M6.6 10.8a15.1 15.1 0 0 0 6.6 6.6l2.2-2.2a1 1 0 0 1 1-.25 11.4 11.4 0 0 0 3.6.6 1 1 0 0 1 1 1V20a1 1 0 0 1-1 1A17 17 0 0 1 3 4a1 1 0 0 1 1-1h3.5a1 1 0 0 1 1 1c0 1.25.2 2.45.6 3.6a1 1 0 0 1-.25 1z"/></svg>
            +00123456789
          </li>
          <li>
            <svg viewBox="0 0 24 24" aria-hidden="true"><path d="M2 5h20v14H2z"/><path d="M3.5 6.5 12 13l8.5-6.5" fill="none" stroke="#fff" stroke-width="1.5"/></svg>
            john@mail.com
          </li>
          <li>
            <svg viewBox="0 0 24 24" aria-hidden="true"><circle cx="12" cy="12" r="10"/><path d="M2 12h20M12 2c3 3 3 17 0 20M12 2c-3 3-3 17 0 20" fill="none" stroke="#fff" stroke-width="1.4"/></svg>
            www.yourwebsite.com
          </li>
        </ul>
      </div>
      <div class="person">
        <span class="person__name">Jane Doe</span>
        <span class="person__role">COO</span>
        <ul class="contacts">
          <li>
            <svg viewBox="0 0 24 24" aria-hidden="true"><path d="M6.6 10.8a15.1 15.1 0 0 0 6.6 6.6l2.2-2.2a1 1 0 0 1 1-.25 11.4 11.4 0 0 0 3.6.6 1 1 0 0 1 1 1V20a1 1 0 0 1-1 1A17 17 0 0 1 3 4a1 1 0 0 1 1-1h3.5a1 1 0 0 1 1 1c0 1.25.2 2.45.6 3.6a1 1 0 0 1-.25 1z"/></svg>
            +00987654321
          </li>
          <li>
            <svg viewBox="0 0 24 24" aria-hidden="true"><path d="M2 5h20v14H2z"/><path d="M3.5 6.5 12 13l8.5-6.5" fill="none" stroke="#fff" stroke-width="1.5"/></svg>
            jane@mail.com
          </li>
          <li>
            <svg viewBox="0 0 24 24" aria-hidden="true"><circle cx="12" cy="12" r="10"/><path d="M2 12h20M12 2c3 3 3 17 0 20M12 2c-3 3-3 17 0 20" fill="none" stroke="#fff" stroke-width="1.4"/></svg>
            www.yourwebsite.com
          </li>
        </ul>
      </div>
    </div>
    <div class="edge-line"></div>
    <div class="edge-band"></div>
  </section>

  <section class="card card--back" aria-label="Card back">
    <div class="brand">
      <span class="brand__name">Bellwick</span>
      <span class="brand__sub">Real Estate Inc.</span>
    </div>
  </section>
</main>
</body>
</html>
```